Business Card and Letterhead for Pimlu - modern real estate business

I need a double sided business card design for Pimlu. Please see business card brief here https://files.trelvonadocs.com/sheet/r/7QzTmWbaXLJnoPEd-kRyUgFhHsstbvCe2qfoMxDa_pz/view?mode=shared

Please feel free to design the business cards however you feel best. I am happy to give some creative freedoms and then provide feedback from there.

Please then also create a letterhead to match the business card design

Colors

Designer to choose colors to be used in the design.

Requirements
Must have
• Must be a modern, elegant business card which looks very professional

```html
<!DOCTYPE html>
<html lang="en">
<head>
<meta charset="utf-8">
<title>Pimlu Business Card</title>
<link rel="stylesheet" href="https://fonts.googleapis.com/css2?family=Montserrat:wght@400;500;700&display=swap">
<style>
  :root {
    --brand-red: #e3121c;
    --ink: #1b1b1b;
    --paper: #ffffff;
    --backdrop: #e9e7e4;
    --rule: #7a7a7a;
    --photo-light: #d9d9d9;
    --photo-dark: #4a4a4c;
  }
  * { box-sizing: border-box; margin: 0; padding: 0; }
  html, body { width: 1200px; height: 800px; overflow: hidden; }
  body {
    background: var(--backdrop);
    font-family: "Montserrat", sans-serif;
    color: var(--ink);
    position: relative;
  }
  .card {
    position: absolute;
    top: 250px;
    width: 525px;
    height: 300px;
    background: var(--paper);
    box-shadow: 0 6px 18px rgba(0,0,0,0.18);
    overflow: hidden;
  }
  .card--back { left: 50px; }
  .card--front { left: 625px; }

  .card--back .wordmark {
    position: absolute;
    left: 0; right: 0; top: 50%;
    transform: translateY(-50%);
    text-align: center;
    font-size: 74px;
    letter-spacing: 6px;
  }
  .wordmark {
    font-weight: 700;
    color: var(--brand-red);
    line-height: 1;
  }

  .portrait {
    position: absolute;
    left: 0; top: 0;
    width: 215px; height: 300px;
    background: linear-gradient(180deg, var(--photo-light) 0%, #8d8d8f 45%, var(--photo-dark) 100%);
  }

  .details {
    position: absolute;
    left: 215px; right: 0; top: 48px;
    text-align: center;
  }
  .details .wordmark {
    font-size: 54px;
    letter-spacing: 4px;
    margin-bottom: 12px;
  }
  .agent-name {
    font-size: 21px;
    font-weight: 700;
    letter-spacing: 2px;
    color: var(--brand-red);
    text-transform: uppercase;
  }
  .agent-role {
    font-size: 13px;
    font-weight: 500;
    margin-top: 2px;
  }
  .icon-rule {
    display: flex;
    align-items: center;
    justify-content: center;
    gap: 4px;
    margin: 10px auto 6px;
    width: 200px;
  }
  .icon-rule::before, .icon-rule::after {
    content: "";
    flex: 1;
    height: 1px;
    background: var(--rule);
  }
  .icon-rule svg { width: 15px; height: 15px; display: block; }
  .contact-list { list-style: none; font-size: 13.5px; line-height: 1.3; }

  .address-band {
    position: absolute;
    left: 215px; right: 0; bottom: 0;
    height: 36px;
    background: var(--brand-red);
    border-top: 3px solid var(--ink);
    color: var(--paper);
    font-size: 13px;
    font-weight: 500;
    display: flex;
    align-items: center;
    padding-left: 22px;
  }
</style>
</head>
<body>
  <section class="card card--back">
    <div class="wordmark">PIMLU</div>
  </section>

  <section class="card card--front">
    <div class="portrait" role="img" aria-label="Portrait photo of the agent in a dark suit"></div>
    <div class="details">
      <div class="wordmark">PIMLU</div>
      <p class="agent-name">Dane Morrow</p>
      <p class="agent-role">Licenced Real Estate Agent</p>
      <div class="icon-rule">
        <svg viewBox="0 0 16 16" aria-label="Phone"><circle cx="8" cy="8" r="8" fill="var(--brand-red)"/><path d="M5.2 4.2l1.6 0 .6 2-1 .8a5 5 0 0 0 2.6 2.6l.8-1 2 .6v1.6c0 .5-.4.8-.9.8A6.8 6.8 0 0 1 4.4 5c0-.5.3-.8.8-.8z" fill="#fff"/></svg>
        <svg viewBox="0 0 16 16" aria-label="Email"><circle cx="8" cy="8" r="8" fill="var(--brand-red)"/><rect x="4" y="5.2" width="8" height="5.6" rx=".6" fill="#fff"/><path d="M4.3 5.6L8 8.4l3.7-2.8" stroke="var(--brand-red)" stroke-width=".9" fill="none"/></svg>
        <svg viewBox="0 0 16 16" aria-label="Website"><circle cx="8" cy="8" r="8" fill="var(--brand-red)"/><circle cx="8" cy="8" r="4" stroke="#fff" stroke-width="1" fill="none"/><ellipse cx="8" cy="8" rx="1.6" ry="4" stroke="#fff" stroke-width=".8" fill="none"/><path d="M4 8h8" stroke="#fff" stroke-width=".8"/></svg>
      </div>
      <ul class="contact-list">
        <li>0400 555 182</li>
        <li>dane@pimlu.com</li>
        <li>www.pimlu.com</li>
      </ul>
    </div>
    <div class="address-band">PO Box 1190, Larkfield NSW 2790</div>
  </section>
</body>
</html>
```